Design a Job Application & CV

I need a design for upcoming job applications that includes a cv. It needs to look as elegant and modern as possible as the application will be send mainly to large corporations and strategy consultancies. I have attached an application that I like for your consideration. One of the more difficult requirements is that it needs to be editable in ms office word for mac/windows.
As stated only the design is part of this project. I will fill in my content later on.
Reason: Dear Designers,
I am going to increase the budget as well as extending the deadline. I am hoping that you can improve upon the design that I have provided in the brief. If you have questions please let me know.
Dear Designers,
Target Market(s)
Human Resources Managers, Senior Consultants and Executives of larger firms
Industry/Entity Type
Office
Requirements
Must have
- 4 Pages including( a cover page, a coverletter page, 2 pages cv)
It should be easy to edit and should be readable by word for mac, i.e. in the *.docx format.
Here is an example of what I like:
http://www.torvenmald.example/applicationexample.pdf
http://www.torvenmald.example/applicationExample.docx
colors that I like are blue, grey, black, white
Nice to have
- icons to indicate sections
Should not have
- invasive cliparts

```html
<!DOCTYPE html>
<html lang="en">
<head>
<meta charset="utf-8">
<title>Profile &amp; CV</title>
<link rel="stylesheet" href="https://fonts.googleapis.com/css2?family=Advent+Pro:wght@300;400&family=Crimson+Text:wght@400&display=swap">
<style>
  :root {
    --blue: #1596d2;
    --grey: #6b6c70;
    --ink: #1e1e1e;
    --name: #4a4a4a;
    --paper: #ffffff;
  }
  * { margin: 0; padding: 0; box-sizing: border-box; }
  html, body { width: 848px; height: 1200px; overflow: hidden; background: var(--paper); }
  .page {
    position: relative;
    width: 848px;
    height: 1200px;
    overflow: hidden;
    background: var(--paper);
    font-family: "Crimson Text", Georgia, serif;
    color: var(--ink);
    font-size: 13.5px;
  }
  .header-band, .footer-band { position: absolute; left: 0; width: 848px; display: block; }
  .header-band { top: 0; height: 97px; }
  .footer-band { bottom: 0; height: 32px; }
  .page-title {
    position: absolute;
    left: 32px;
    top: 14px;
    font-family: "Advent Pro", "Helvetica Neue", sans-serif;
    font-weight: 300;
    font-size: 56px;
    letter-spacing: 1px;
    color: var(--paper);
  }
  .person-name {
    position: absolute;
    left: 34px;
    top: 131px;
    font-family: "Advent Pro", "Helvetica Neue", sans-serif;
    font-weight: 300;
    font-size: 22px;
    letter-spacing: 1px;
    text-transform: uppercase;
    color: var(--name);
  }
  .cv-row {
    position: absolute;
    left: 34px;
    width: 780px;
    display: flex;
    line-height: 25px;
  }
  .cv-label { width: 352px; flex: none; }
  .cv-value p { white-space: nowrap; }
  .cv-value .gap { margin-top: 25px; }
</style>
</head>
<body>
<main class="page">
  <svg class="header-band" viewBox="0 0 848 97" aria-hidden="true">
    <polygon points="0,0 626,0 612,97 0,97" fill="var(--blue)"/>
    <polygon points="638,0 848,0 848,97 624,97" fill="var(--grey)"/>
  </svg>
  <h1 class="page-title">Profile &amp; CV</h1>

  <h2 class="person-name">Marisa Valcourt</h2>

  <section class="cv-row" style="top:170px">
    <div class="cv-label"><p>Nationality:</p><p>Age:</p><p>Date of Birth:</p><p>Marital Status:</p></div>
    <div class="cv-value"><p>Brazilian</p><p>24</p><p>13.05.1976</p><p>Single</p></div>
  </section>

  <section class="cv-row" style="top:294px">
    <div class="cv-label">Address in Brazil:</div>
    <div class="cv-value"><p>Rua das Acácias 27,&nbsp; Belo Horizonte, Brazil</p></div>
  </section>

  <section class="cv-row" style="top:345px">
    <div class="cv-label">Address in Britain:</div>
    <div class="cv-value"><p>14 Larkfield Road, Hollowmere, London SE9 2QT</p></div>
  </section>

  <section class="cv-row" style="top:395px">
    <div class="cv-label">Education:</div>
    <div class="cv-value">
      <p>Aurora Vale University of Communications , São Paulo, Brazil</p>
      <p>Degree in Publicity and Advertising, completed in 1998</p>
      <p class="gap">Subjects studied: Communications, Advertising, Marketing, Media</p>
      <p class="gap">Buying, Public Relations.</p>
    </div>
  </section>

  <section class="cv-row" style="top:569px">
    <div class="cv-label">Work Experience</div>
    <div class="cv-value">
      <p>Pitchline Sports Ltd (Sports Store)</p>
      <p>Period: 03/99 - 02/00</p>
      <p>Marketing and Administration Manager for Sports Store.</p>
      <p class="gap">Clearview Impact (Marketing Consultancy)</p>
      <p>Period: 06/98 - 10/98</p>
      <p>Promotion and Marketing for a radio show called "Wellness Hour"</p>
      <p class="gap">Ferraz Trading (Import &amp; Export Company)</p>
      <p>Period: 09/97 - 12/97</p>
      <p>Administrative Assistant</p>
      <p class="gap">Nova Propaganda Ltda. (Advertising Company )</p>
      <p>Period: 08/96 - 02/97</p>
      <p>Marketing and Production Assistant</p>
    </div>
  </section>

  <section class="cv-row" style="top:995px">
    <div class="cv-label">IT Experience</div>
    <div class="cv-value" style="margin-left:-4px">
      <p>DeskOS, VectorDraw , LayoutPro , OfficeSuite</p>
      <p>Basic knowledge of MacroDesk Programmes</p>
    </div>
  </section>

  <section class="cv-row" style="top:1097px">
    <div class="cv-label">Languages Spoken</div>
    <div class="cv-value">
      <p>Portuguese (mother tongue)</p>
      <p>English (Westbury First Certificate)</p>
    </div>
  </section>

  <svg class="footer-band" viewBox="0 0 848 32" aria-hidden="true">
    <polygon points="0,0 211,0 232,32 0,32" fill="var(--grey)"/>
    <polygon points="218,0 848,0 848,32 240,32" fill="var(--blue)"/>
  </svg>
</main>
</body>
</html>
```